Various Designs

We need various designs for our new hand disinfectant dispensers that feature three extra-large windows that allow users to customize the appearance simply by changing the graphics.
Each dispenser has one window at the front and one on each side. The front window can have two different sizes. Please refer to attached zip file named Dispenser_Design_Templates.
The designs should be fresh and of high quality. Please don't just place a photo and spam me.
The design should also contain our logo (PVM Switzerland - is included in the template).
The design should further be professional enough for a medical and public setting. The dispensers will be used in hospitals, medical facilities, old pension homes, schools, restaurants, kitchens, public places etc.
We value creativity a lot!
It would be great if the dispenser features a slogan such as "Hand Hygiene Saves Lives". I have added a number of slogans at the end of this description.
Do not use dark colors such as brown. These colors do not stand for hygiene. You can use black but only in conjunction with a bright color.
The following files contain designs that I like:
- 01w
- velunadecor
- worldwide
- IMG_0137
Slogans:
- Hand Hygiene Saves Lives
- Did you wash your hands?
- Did you disinfect your hands?
- Protect Yourself and Your Patients
- Healthy Hands Start Here
- Hand Hygiene We Love... We Care... We Share...
- Clean hands prevent germs from spreading.
- Practice Good Hand Hygiene
- Save Lives: Clean Your Hands
- Save Lives: Disinfect Your Hands
- Washing Hands Saves Lives
- Wash Your Hands Please
- Be aware…..!!!!! Wash with care…..!!!!!
- Hand Hygiene Station
- Hand Hygiene Share your care, not your germs
- Good Hand Hygiene It's Critical Sanitize Wash Moisturize
- Disinfect (image of a hand)
- Clean (image of a hand)
- No Water? No Problem. Waterless Hand Rub. Keep it Handy.
- Wash your hands! If not for yourself, then do it for them.
- Practice good hygiene - it-s contagious!
- Be aware, wash with care!
- Filthy fingers forecast sickness and sadness.
- Hand Hygiene The power is in your hands
- Bury the germ, Wash your hands
- Sanitize your hands and support our clean hands initiative
- Sanitize your hands. Together we can make a difference.
- You are grand if you wash your hand.
- Holding hands feels better when they’re clean.
- Be wise wash hands often.
- Wash those germs away!!!
- Your Hands Can Be Dangerous. Disinfect them to keep germs away.
- Ten out of ten patients prefer care from clean hands.
- Safety first, disinfect and protect
- It’s universal- handwashing every patient every time!
- Infection control is in your hands.
- Make your intention prevention. Wash your hands

```html
<!DOCTYPE html>
<html lang="en">
<head>
<meta charset="utf-8">
<title>PVM Switzerland – Hygiene Serene Dispenser Panel</title>
<link href="https://fonts.googleapis.com/css2?family=Fredoka:wght@600&family=PT+Sans:wght@400&display=swap" rel="stylesheet">
<style>
  :root {
    --paper: #ffffff;
    --sun-yellow: #f5cd36;
    --sun-warm: #f1c23e;
    --peach: #e9a97c;
    --lavender: #9a6cbf;
    --brand-purple: #7b3f98;
    --cut-line: #d8353a;
    --safe-line: #7cc25a;
  }
  html, body {
    margin: 0;
    padding: 0;
    width: 1200px;
    height: 1000px;
    overflow: hidden;
    background: var(--paper);
  }
  .panel {
    position: relative;
    width: 1200px;
    height: 1000px;
    background: var(--paper);
  }
  .artwork, .template-guides {
    position: absolute;
    inset: 0;
  }
  .slogan {
    position: absolute;
    top: 54px;
    left: 350px;
    width: 510px;
    margin: 0;
    text-align: center;
    font-family: "Fredoka", sans-serif;
    font-weight: 600;
    font-size: 45px;
    line-height: 51px;
    color: var(--peach);
    text-shadow: -3px 3px 0 var(--lavender);
  }
  .brand {
    position: absolute;
    left: 424px;
    top: 812px;
    display: flex;
    align-items: center;
    gap: 18px;
    font-family: "PT Sans", sans-serif;
    font-weight: 400;
    color: var(--brand-purple);
  }
  .brand-name {
    font-size: 76px;
    line-height: 82px;
    letter-spacing: 22px;
  }
  .brand-country {
    font-size: 24px;
    line-height: 26px;
    margin-top: 8px;
  }
</style>
</head>
<body>
<main class="panel">
  <svg class="artwork" width="1200" height="1000" viewBox="0 0 1200 1000">
    <defs>
      <clipPath id="print-area">
        <rect x="210" y="0" width="778" height="1000"/>
      </clipPath>
      <radialGradient id="globe-tone" gradientUnits="userSpaceOnUse" cx="600" cy="640" r="560">
        <stop offset="0" stop-color="var(--sun-yellow)"/>
        <stop offset="0.55" stop-color="var(--sun-warm)"/>
        <stop offset="0.8" stop-color="var(--peach)"/>
        <stop offset="1" stop-color="var(--lavender)"/>
      </radialGradient>
      <radialGradient id="haze-tone" cx="0.5" cy="0.5" r="0.5">
        <stop offset="0" stop-color="var(--lavender)" stop-opacity="0.55"/>
        <stop offset="0.6" stop-color="var(--lavender)" stop-opacity="0.3"/>
        <stop offset="1" stop-color="var(--lavender)" stop-opacity="0"/>
      </radialGradient>
    </defs>
    <g clip-path="url(#print-area)" role="img" aria-label="Painted illustration of a large yellow globe covered by peach and purple brush-stroke leaves, with a soft speckled purple haze to the upper right">
      <ellipse class="haze" cx="850" cy="450" rx="190" ry="210" fill="url(#haze-tone)"/>
      <circle class="globe" cx="36" cy="1262" r="1098" fill="url(#globe-tone)"/>
    </g>
  </svg>

  <h1 class="slogan">BE<br>Hygiene Serene.<br>Keep Your Hands<br>CLEAN.</h1>

  <div class="brand">
    <span class="brand-name">PVM</span>
    <span class="brand-country">Switzerland</span>
  </div>

  <svg class="template-guides" width="1200" height="1000" viewBox="0 0 1200 1000" fill="none">
    <path class="cut-outline" d="M212 0 L988 0 L888 1000 L312 1000 Z" stroke="var(--cut-line)" stroke-width="2"/>
    <path class="safe-zone" d="M276 130 Q276 72 340 58 Q600 0 860 58 Q924 72 922 130 L858 880 Q850 955 780 964 Q600 985 420 964 Q358 955 352 880 Z" stroke="var(--safe-line)" stroke-width="2"/>
    <g class="mount-holes" stroke="var(--cut-line)" stroke-width="2">
      <circle cx="266" cy="38" r="10"/>
      <circle cx="931" cy="38" r="10"/>
      <circle cx="349" cy="950" r="10"/>
      <circle cx="848" cy="950" r="10"/>
    </g>
  </svg>
</main>
</body>
</html>
```